IT consulting company looking for a modern business design for a website and a new logo

We are the IT-consulting company VelmaTrix from Germany and need a new and modern business website and a new logo. We are specialized in output management. Our services include business analysis, outsourcing, development, training and project leading. We wish for a design with nature pictures (mountains, lakes, rivers, forests, etc.) for our company with the colors green and blue. If it is possible, a slow-mo video of a nature scene. The design should be responsive and the menu should change to a hamburger menu. The following are: • Services / Solutions 1. Output Management 2. Outsourcing 3. Development 4. Business Analyst 5. Training • Partners • Careers • About Us 1. Project A 2. Project B 3. Project C • Contact Notes for the following categories: For "Services / Solutions" we want to conclude some contents from all the sub-points and sub-points below. Additionally, we would like to see some sub-point under "Services / Solutions". For Output Management: "5 Benefits of Output Management Systems (OMS) - OMS Simplifies and Accelerates External Communication - Helps Reduce Communication Mistakes - Provides Customers With Fast and Secure Responses to your questions - Employees can focus on the essential as they can access prepared templates - Companies get complete transparency about their communication "The point" partner does not have sub-points. The content here is a quote and the logo from the company Brel. For now, just placeholders on this site. The next point wants to be "career" without sub-point and wants to contain some text. Carrer options wants to be listed here. Next point wants to be "About us", where we need sub-points which we do not know exactly at this moment, but they will contain text. By clicking directly on "About us" we want to include pictures and texts about 6 employees for which we only need placeholders at the moment. The last point wants to be "contact", where customers can send us messages. The main page should include a story about our company, which can be a placeholder for now. For reference, designs have a look at: https://brelvanto.de/ https://www.tarnopix.com/ https://www.pldrive.de/ We prefer WordPress designs, created with the plugin ELEMENTOR, so that we can easily edit the content by ourselves. The final design should look professional, competent and modern.

Target Market(s)

With our website, we want to reach the following target groups. <br> <br> <br> <br> <br> <br> <br> <br> <br> <br> <br> <br> <br> <br> <br> <br> <br> <br> <br> <br> <br> <br> <br> <br> <br> <br> <br> <br> <br> <br> <br> <br> <br> <br> <br> <br> <br> <br> <br> <br> <br> <br> <br> <br> <br> <br> <br> <br> <br>

Industry/Entity Type

Consulting

Logo Text

(optionally) VelmaTrix

Font styles to use
Sans Serif

Colors

Designer to choose colors to be used in the design.

Requirements
Must have
• 1. Outsourcing 3. Development 4. Business Analyst 5. Training • Partners • Careers • About Us 1. Project A 2. Project B 3. Project C • Contact The above-mentioned background picture with nature motifs (mountains, lakes, rivers, forests, etc.). WordPress design in primary colors blue and green.
Nice to have
• ELEMENTOR template. Effects for the background pictures. Counter of all successful projects for Output Management, Business Analyst and Training

```html
<!DOCTYPE html>
<html lang="en">
<head>
<meta charset="utf-8">
<title>VelmaTrix – IT Consulting</title>
<link rel="stylesheet" href="https://fonts.googleapis.com/css2?family=Montserrat:wght@400;500;700&family=Open+Sans:wght@400;600&display=swap">
<style>
:root{
  --green:#3aa33a;
  --blue:#1a86d0;
  --band:#e3eff5;
  --text:#3c3c3c;
  --muted:#777;
  --slate:#5b7f8f;
  --title-faint:#a1bdca;
  --dark:#2b2b2b;
  --white:#fff;
}
*{box-sizing:border-box;margin:0;padding:0}
html,body{width:1200px;height:4019px;overflow:hidden}
body{font-family:"Open Sans",Arial,sans-serif;color:var(--text);background:var(--white);font-size:13px}
h2.section-title{font-family:"Montserrat",Arial,sans-serif;font-weight:400;color:var(--green);font-size:32px;text-align:center}
.lead{text-align:center;font-size:13px;line-height:22.5px;color:var(--text);width:916px;margin:0 auto}
.btn{display:block;margin:0 auto;background:var(--blue);color:var(--white);font-size:12px;text-transform:uppercase;text-align:center;line-height:38px;height:38px;width:104px;text-decoration:none}

/* header */
.site-header{height:80px;position:relative}
.brand{position:absolute;left:142px;top:16px;font-family:"Montserrat",Arial,sans-serif;font-size:38px;color:var(--green);font-weight:400}
.main-nav{position:absolute;right:145px;top:32px;display:flex;gap:33px}
.main-nav a{font-size:12.5px;color:#666;text-decoration:none;text-transform:uppercase}
.main-nav a.active{color:var(--blue)}

/* hero: lake at sunset, treeline, reeds */
.hero{height:534px;position:relative;overflow:hidden;
  background:
    radial-gradient(ellipse 220px 120px at 52% 4%,rgba(255,236,170,.95) 0%,rgba(240,200,120,.55) 40%,rgba(200,160,90,0) 100%),
    radial-gradient(ellipse 260px 200px at 55% 72%,rgba(235,190,110,.75) 0%,rgba(190,140,70,.35) 45%,rgba(120,90,50,0) 100%),
    linear-gradient(180deg,#26301f 0%,#3b4128 18%,#4d4a30 30%,#7a6a45 44%,#8f7a4e 55%,#6b5a3a 66%,#3f4a2e 80%,#2d3a22 100%)}
.hero-shade{position:absolute;inset:0;background:linear-gradient(90deg,rgba(20,25,15,.45) 0%,rgba(20,25,15,0) 30%,rgba(20,25,15,0) 70%,rgba(20,25,15,.45) 100%)}
.play{position:absolute;left:50%;top:318px;transform:translate(-50%,-50%)}
.hero-caption{position:absolute;top:356px;width:100%;text-align:center;font-family:"Montserrat",Arial,sans-serif;font-size:30px;color:var(--white)}

/* welcome */
.welcome{height:318px;padding-top:76px}
.welcome .lead{margin-top:14px}
.welcome .btn{margin-top:14px}

/* services */
.services{height:716px;background:var(--band);position:relative}
.services-heading{position:absolute;left:142px;top:62px;font-family:"Montserrat",Arial,sans-serif;font-weight:700;font-size:72px;color:var(--title-faint)}
.service-list{position:absolute;left:142px;top:162px;list-style:none}
.service-list li{height:72px;display:flex;align-items:center;font-family:"Montserrat",Arial,sans-serif;font-size:33px;color:var(--slate)}
.service-list li svg{margin-right:8px}
.service-list li.active{color:var(--green)}
.service-divider{position:absolute;left:480px;top:171px;width:3px;height:317px;background:var(--title-faint)}
.service-divider span{position:absolute;left:0;bottom:0;width:3px;height:40px;background:var(--green)}
.service-media{position:absolute;left:523px;top:171px;width:533px;height:240px;background:
  radial-gradient(ellipse 120px 60px at 88% 30%,rgba(190,70,50,.55) 0%,rgba(190,70,50,0) 100%),
  radial-gradient(ellipse 160px 60px at 30% 95%,rgba(80,120,170,.5) 0%,rgba(80,120,170,0) 100%),
  linear-gradient(135deg,#2b2e33 0%,#4a4f56 45%,#6b6e72 70%,#3a3c40 100%)}
.service-media .play{top:120px}
.oms-benefits{position:absolute;left:523px;top:430px;list-style:none}
.oms-benefits li{font-size:12.5px;line-height:32px;padding-left:11px;position:relative}
.oms-benefits li:before{content:"•";position:absolute;left:0}
.services .btn{position:absolute;left:523px;top:597px;margin:0}

/* partners */
.partners{height:592px;padding-top:72px;position:relative}
.quote{text-align:center;font-size:16px;line-height:27px;color:var(--muted);width:916px;margin:14px auto 0}
.quote-author{text-align:center;color:var(--blue);font-size:16px;font-weight:600;margin-top:11px}
.partner-grid{display:grid;grid-template-columns:repeat(6,161px);grid-auto-rows:50px;width:966px;margin:40px auto 0;align-items:center}
.partner{font-weight:600;font-size:12.5px;color:#6d6d6d;text-align:center}

/* career */
.career{height:513px;background:var(--band);padding-top:72px}
.career .lead{margin-top:12px}
.jobs{display:flex;gap:16px;width:914px;margin:28px auto 0}
.job{width:170px;height:167px;background:var(--white);border:1px solid #cfdde4;padding:14px 14px 0}
.job h3{font-family:"Montserrat",Arial,sans-serif;font-weight:400;color:var(--green);font-size:15px}
.job h4{font-weight:400;font-size:11px;margin-top:5px}
.job p{font-size:9px;line-height:14px;color:#888;margin-top:10px}
.job a{display:block;margin-top:13px;font-size:12px;font-weight:600;color:var(--blue);text-decoration:none}
.career .btn{margin-top:24px}

/* about */
.about{height:585px;padding-top:72px}
.about .lead{margin-top:14px}
.about .btn{margin-top:14px}
.staff-title{text-align:center;font-family:"Montserrat",Arial,sans-serif;font-weight:400;font-size:18px;margin-top:30px}
.staff{display:flex;gap:10px;width:914px;margin:14px auto 0}
.member{width:144px;text-align:center}
.portrait{height:160px}
.p-daniel{background:radial-gradient(ellipse 60px 70px at 50% 45%,#a88a78 0%,#6e5548 55%,rgba(110,85,72,0) 100%),linear-gradient(180deg,#e4e4e4 0%,#c9c9c9 60%,#3a3a3a 100%)}
.p-sophia{background:radial-gradient(ellipse 60px 75px at 50% 45%,#caa08a 0%,#7a5a46 55%,rgba(122,90,70,0) 100%),linear-gradient(180deg,#d6d2ca 0%,#bdb8b0 60%,#7a6f66 100%)}
.p-alexander{background:radial-gradient(ellipse 55px 65px at 50% 42%,#c49d86 0%,#6b5547 55%,rgba(107,85,71,0) 100%),linear-gradient(180deg,#e6e6e6 0%,#cfcfcf 55%,#1f1f1f 100%)}
.p-olivia{background:radial-gradient(ellipse 60px 70px at 50% 45%,#d6b08f 0%,#c8a064 55%,rgba(200,160,100,0) 100%),linear-gradient(180deg,#b8c0c4 0%,#8e979c 60%,#3f8db8 100%)}
.p-jayden{background:radial-gradient(ellipse 60px 70px at 50% 45%,#b08a72 0%,#4a3a30 55%,rgba(74,58,48,0) 100%),linear-gradient(180deg,#cfd3d6 0%,#9aa0a5 60%,#2f5c8a 100%)}
.p-isabella{background:radial-gradient(ellipse 60px 75px at 52% 45%,#d2a98c 0%,#8a5f44 55%,rgba(138,95,68,0) 100%),linear-gradient(180deg,#d8d4cf 0%,#b9b2ab 60%,#6a5546 100%)}
.member h3{font-weight:400;font-size:13px;color:var(--blue);margin-top:6px}
.member p{font-size:10px;color:#555}

/* contact */
.contact{height:441px;background:var(--band);padding-top:78px}
.contact-form{width:914px;margin:28px auto 0}
.row{display:flex;gap:13px}
.field{flex:1;height:38px;background:var(--white);border:1px solid #c9d6dc;font-size:11px;color:#888;padding:11px 14px}
.message{height:118px;margin-top:17px}
.contact .btn{width:80px;margin-top:18px}

/* footer */
.site-footer{height:240px;background:var(--dark);color:#ccc;position:relative}
.foot-col{position:absolute;top:42px}
.foot-col h3{font-family:"Montserrat",Arial,sans-serif;font-weight:400;font-size:18px;color:var(--white)}
.foot-links{display:grid;grid-template-columns:64px 64px;margin-top:14px;font-size:10px;line-height:22px}
.foot-col p{font-size:10px;line-height:22px}
.foot-col .info{margin-top:14px}
.social{display:flex;gap:11px;margin-top:14px}
.social span{width:24px;height:24px;border-radius:50%;background:var(--blue);display:block}
.foot-rule{position:absolute;left:142px;right:144px;top:169px;height:1px;background:#555}
.copyright{position:absolute;top:192px;width:100%;text-align:center;font-size:10px;color:#bbb}
</style>
</head>
<body>

<header class="site-header">
  <div class="brand">VelmaTrix</div>
  <nav class="main-nav">
    <a class="active" href="#about">About Us</a>
    <a href="#services">Services</a>
    <a href="#partners">Partners</a>
    <a href="#career">Career</a>
    <a href="#contact">Contact</a>
  </nav>
</header>

<section class="hero" role="img" aria-label="Slow-motion video of a forest lake at sunset, sun glowing above the treeline and reflecting on the water, with reeds in the foreground">
  <div class="hero-shade"></div>
  <svg class="play" width="40" height="40" viewBox="0 0 40 40"><circle cx="20" cy="20" r="20" fill="#fff"/><path d="M16 12 L28 20 L16 28 Z" fill="#222"/></svg>
  <div class="hero-caption">Praesent scelerisque fermentum mauris</div>
</section>

<section class="welcome">
  <h2 class="section-title">Welcome to VelmaTrix</h2>
  <p class="lead">Pellentesque accumsan ut metus sed elementum. Integer ac ante neque. Vestibulum a eleifend sapien, at consectetur risus. Nulla finibus lacinia dolor, semper dictum leo eleifend non. Etiam non nulla non turpis pharetra tincidunt sed ut lorem. Etiam bibendum eros at velit consectetur commodo. Ut auctor convallis ligula a finibus. Fusce lacinia rutrum nunc at vulputate. Quisque arcu erat, cursus a urna dictum.</p>
  <a class="btn" href="#">Read More</a>
</section>

<section class="services" id="services">
  <div class="services-heading">Services</div>
  <ul class="service-list">
    <li><svg width="26" height="26" viewBox="0 0 26 26"><rect x="3" y="3" width="20" height="20" fill="none" stroke="#5b7f8f" stroke-width="2"/><path d="M7 18v-4M12 18v-8M17 18v-6" stroke="#5b7f8f" stroke-width="2"/></svg>Business Analysis</li>
    <li><svg width="26" height="26" viewBox="0 0 26 26"><circle cx="13" cy="9" r="4" fill="none" stroke="#5b7f8f" stroke-width="2"/><path d="M4 23c1-6 17-6 18 0" fill="none" stroke="#5b7f8f" stroke-width="2"/></svg>Outsourcing</li>
    <li><svg width="26" height="26" viewBox="0 0 26 26"><circle cx="13" cy="13" r="9" fill="none" stroke="#5b7f8f" stroke-width="2"/><path d="M9 13l3 3 5-6" fill="none" stroke="#5b7f8f" stroke-width="2"/></svg>Development</li>
    <li><svg width="26" height="26" viewBox="0 0 26 26"><rect x="3" y="5" width="20" height="14" fill="none" stroke="#5b7f8f" stroke-width="2"/><path d="M9 23h8" stroke="#5b7f8f" stroke-width="2"/></svg>Trainings</li>
    <li class="active"><svg width="26" height="26" viewBox="0 0 26 26"><path d="M13 3l8 18H5z" fill="none" stroke="#3aa33a" stroke-width="2"/></svg>Project Leading</li>
  </ul>
  <div class="service-divider"><span></span></div>
  <div class="service-media" role="img" aria-label="Video of hands working on a tablet showing charts">
    <svg class="play" width="34" height="34" viewBox="0 0 40 40"><circle cx="20" cy="20" r="20" fill="#fff"/><path d="M16 12 L28 20 L16 28 Z" fill="#222"/></svg>
  </div>
  <ul class="oms-benefits">
    <li>OMS simplifies and speeds up communication with the outside world.</li>
    <li>Helps to reduce errors in communication.</li>
    <li>Customers receive quick and secure answers to their questions.</li>
    <li>Employees can focus on the essential as they are on prepared templates can access.</li>
    <li>Companies get complete transparency about their communication</li>
  </ul>
  <a class="btn" href="#">Read More</a>
</section>

<section class="partners" id="partners">
  <h2 class="section-title">Partner</h2>
  <p class="quote">" Suspendisse dapibus eros massa, ac iaculis ipsum venenatis sed. Pellentesque scelerisque auctor erat, at faucibus enim sollicitudin condimentum. Suspendisse eu enim ut lectus cursus commodo aliquet porta eros. Aenean tortor metus, venenatis eu luctus et, aliquet at tortor. "</p>
  <p class="quote-author">Mara Lenz, Orvalis</p>
  <svg style="position:absolute;left:54px;top:152px" width="16" height="26" viewBox="0 0 16 26"><path d="M13 2L3 13l10 11" fill="none" stroke="#999" stroke-width="2"/></svg>
  <svg style="position:absolute;left:1128px;top:152px" width="16" height="26" viewBox="0 0 16 26"><path d="M3 2l10 11L3 24" fill="none" stroke="#999" stroke-width="2"/></svg>
  <div class="partner-grid">
    <div class="partner">Orvalis</div><div class="partner">Trevana</div><div class="partner">Sharelyn Fin</div><div class="partner">Banca Verdolia</div><div class="partner">Bank Zarewo</div><div class="partner">Brandeo</div>
    <div class="partner">Calvert Gentry</div><div class="partner">Kelmor</div><div class="partner">Sharelyn</div><div class="partner">Cordan</div><div class="partner">Envira</div><div class="partner">Eurilon</div>
    <div class="partner">Pexalo</div><div class="partner">Fidaro</div><div class="partner">Hulan Bank</div><div class="partner">Generon</div><div class="partner">Hulvana</div><div class="partner">Indro</div>
    <div class="partner">Kavor</div><div class="partner">La Vesta</div><div class="partner">PostLane</div><div class="partner">Metrova</div><div class="partner">Mirelon</div><div class="partner">Monvia</div>
    <div class="partner">Ornel</div><div class="partner">Peachly</div><div class="partner">Coastal Trust</div><div class="partner">Pojistra Group</div><div class="partner">Ling Tao Bank</div><div class="partner">Regiova</div>
  </div>
</section>

<section class="career" id="career">
  <h2 class="section-title">Career</h2>
  <p class="lead">Pellentesque accumsan ut metus sed elementum. Integer ac ante neque. Vestibulum a eleifend sapien, at consectetur risus. Nulla finibus lacinia dolor, semper dictum leo eleifend non. Etiam non nulla non turpis pharetra tincidunt sed ut lorem. Etiam bibendum eros at velit consectetur commodo. Ut auctor convallis ligula a finibus. Fusce lacinia rutrum nunc at vulputate. Quisque arcu erat, cursus a urna dictum.</p>
  <div class="jobs">
    <article class="job"><h3>Fusce sodales</h3><h4>Quisque gravida rhoncus</h4><p>Donec augue odio, varius quis sem at, pretium malesuada sapien. In pellentesque sem ultricies lorem molestie.</p><a href="#">APPLY NOW</a></article>
    <article class="job"><h3>Vivamus suada</h3><h4>Quisque gravida rhoncus</h4><p>Donec augue odio, varius quis sem at, pretium malesuada sapien. In pellentesque sem ultricies lorem molestie.</p><a href="#">APPLY NOW</a></article>
    <article class="job"><h3>Donec augue</h3><h4>Quisque gravida rhoncus</h4><p>Donec augue odio, varius quis sem at, pretium malesuada sapien. In pellentesque sem ultricies lorem molestie.</p><a href="#">APPLY NOW</a></article>
    <article class="job"><h3>Etiam sodales</h3><h4>Quisque gravida rhoncus</h4><p>Donec augue odio, varius quis sem at, pretium malesuada sapien. In pellentesque sem ultricies lorem molestie.</p><a href="#">APPLY NOW</a></article>
    <article class="job"><h3>Quisque tincidunt</h3><h4>Quisque gravida rhoncus</h4><p>Donec augue odio, varius quis sem at, pretium malesuada sapien. In pellentesque sem ultricies lorem molestie.</p><a href="#">APPLY NOW</a></article>
  </div>
  <a class="btn" href="#">View All</a>
</section>

<section class="about" id="about">
  <h2 class="section-title">About Us</h2>
  <p class="lead">Pellentesque accumsan ut metus sed elementum. Integer ac ante neque. Vestibulum a eleifend sapien, at consectetur risus. Nulla finibus lacinia dolor, semper dictum leo eleifend non. Etiam non nulla non turpis pharetra tincidunt sed ut lorem. Etiam bibendum eros at velit consectetur commodo. Ut auctor convallis ligula a finibus. Fusce lacinia rutrum nunc at vulputate. Quisque arcu erat, cursus a urna dictum.</p>
  <a class="btn" href="#">Read More</a>
  <h3 class="staff-title">Our Staffs</h3>
  <div class="staff">
    <div class="member"><div class="portrait p-daniel" role="img" aria-label="Portrait photo of Daniel, smiling man in a dark shirt on a light grey background"></div><h3>DANIEL</h3><p>Aliquam dignissim</p></div>
    <div class="member"><div class="portrait p-sophia" role="img" aria-label="Portrait photo of Sophia, smiling woman with brown hair"></div><h3>SOPHIA</h3><p>Aliquam dignissim</p></div>
    <div class="member"><div class="portrait p-alexander" role="img" aria-label="Portrait photo of Alexander in a black suit and bow tie"></div><h3>ALEXANDER</h3><p>Aliquam dignissim</p></div>
    <div class="member"><div class="portrait p-olivia" role="img" aria-label="Portrait photo of Olivia, blonde woman with glasses in a blue top"></div><h3>OLIVIA</h3><p>Aliquam dignissim</p></div>
    <div class="member"><div class="portrait p-jayden" role="img" aria-label="Portrait photo of Jayden, smiling man in a blue shirt"></div><h3>JAYDEN</h3><p>Aliquam dignissim</p></div>
    <div class="member"><div class="portrait p-isabella" role="img" aria-label="Portrait photo of Isabella, woman with glasses and auburn hair"></div><h3>ISABELLA</h3><p>Aliquam dignissim</p></div>
  </div>
</section>

<section class="contact" id="contact">
  <h2 class="section-title">Contact Us</h2>
  <div class="contact-form">
    <div class="row">
      <div class="field">First Name</div><div class="field">Last Name</div><div class="field">Email</div><div class="field">Phone</div>
    </div>
    <div class="field message">Message</div>
    <a class="btn" href="#">Submit</a>
  </div>
</section>

<footer class="site-footer">
  <div class="foot-col" style="left:142px">
    <h3>Links</h3>
    <div class="foot-links"><span>Home</span><span>Partners</span><span>About Us</span><span>Career</span><span>Services</span><span>Contact</span></div>
  </div>
  <div class="foot-col" style="left:489px">
    <h3>Contact Info</h3>
    <div class="info"><p>12 Harbor Lane, Street name, City Zipcode</p><p>Phone : 555 014 2290</p><p>Email : info@velmatrix.example</p></div>
  </div>
  <div class="foot-col" style="left:939px">
    <h3>Follow us on</h3>
    <div class="social"><span title="Social network one"></span><span title="Social network two"></span><span title="Social network three"></span></div>
  </div>
  <div class="foot-rule"></div>
  <div class="copyright">Copyright © 2019 VelmaTrix. All rights reserved.</div>
</footer>

</body>
</html>
```